International Business Development Firm, in need of Branded Stationery material

We just made our Logo and now we are looking for branded stationery for our company such as:

* A Letterhead with our company's name, address, and logo at the top in Word format for easy editing
* A more formal letter format with a light background design (watermark) featuring our logo, allowing us to write over it for various documents and presentations
* Business card + Envelopes are a plus but not a must
* PowerPoint for company and product introductions
* An Info sheet with Bullet Points

The design should be professional.
Please ensure the design is high quality and print ready.

Target Market(s)

Businesses and high net value individuels

Industry/Entity Type

International Business Development Firm

Colors

Designer to choose colors to be used in the design.

Requirements
Must have
• word docs so i can use the stationery templates afterwards

```html
<!DOCTYPE html>
<html lang="en">
<head>
<meta charset="utf-8">
<title>Veloria Capital – Stationery</title>
<link rel="stylesheet" href="https://fonts.googleapis.com/css2?family=Lato:wght@400;700&family=Parisienne&display=swap">
<style>
  :root {
    --stage: #ececec;
    --paper: #ffffff;
    --card-dark: #231f20;
    --brand-purple: #5b2d8e;
    --brand-lilac: #8b6bb5;
    --ink: #1d1d1d;
    --window-grey: #dadada;
    --edge: #d4d4d4;
  }
  * { box-sizing: border-box; margin: 0; padding: 0; }
  html, body { width: 1200px; height: 824px; overflow: hidden; }
  body {
    position: relative;
    background: var(--stage);
    font-family: "Lato", sans-serif;
    color: var(--ink);
  }
  .sheet { position: absolute; background: var(--paper); }
  .brand-name {
    font-family: "Lato", sans-serif;
    font-weight: 700;
    color: var(--brand-purple);
    white-space: nowrap;
    display: flex;
    align-items: center;
  }
  .brand-dot {
    display: inline-block;
    border-radius: 50%;
    background: var(--brand-purple);
    flex: none;
  }

  /* Letterhead */
  .letterhead { left: 141px; top: 101px; width: 446px; height: 631px; border: 1px solid var(--edge); }
  .letterhead .brand-name { position: absolute; left: 22px; top: 40px; font-size: 19px; }
  .letterhead .brand-dot { width: 22px; height: 22px; margin-right: 8px; }
  .letterhead .contact-rule { position: absolute; left: 316px; top: 26px; width: 1px; height: 53px; background: var(--brand-purple); }
  .letterhead .contact { position: absolute; left: 328px; top: 24px; font-size: 8.3px; line-height: 10px; }
  .contact .gap { height: 5px; }
  .contact-line { display: flex; align-items: center; gap: 3px; }
  .contact-line svg { width: 6px; height: 6px; flex: none; }
  .letter-body { position: absolute; left: 22px; top: 140px; width: 402px; font-size: 9px; line-height: 10px; }
  .letter-body p { margin-bottom: 11px; text-align: justify; }
  .letter-body .date, .letter-body .block { text-align: left; }
  .letter-body .date { margin-bottom: 12px; }
  .letter-body .block { margin-bottom: 11px; }
  .letter-body .salutation { font-weight: 700; font-size: 11px; margin: 15px 0 12px; }
  .letter-body .regards { margin-top: 22px; }
  .signature { position: absolute; left: 22px; top: 503px; font-family: "Parisienne", cursive; font-size: 21px; color: var(--ink); }

  /* Business cards */
  .card { top: 101px; width: 214px; height: 122px; background: var(--card-dark); border-radius: 9px; }
  .card-front { left: 651px; }
  .card-back { left: 882px; }
  .card-front .brand-name { position: absolute; left: 22px; top: 54px; font-size: 8.5px; }
  .card-front .brand-dot { width: 10px; height: 10px; margin-right: 4px; }
  .card-front .card-rule { position: absolute; left: 111px; top: 31px; width: 1px; height: 60px; background: var(--brand-purple); }
  .card-details { position: absolute; left: 121px; top: 28px; font-size: 5.6px; line-height: 7.6px; color: #fff; }
  .card-details .person { font-size: 8.3px; font-weight: 700; color: var(--brand-purple); line-height: 9px; }
  .card-details .role { color: var(--brand-lilac); margin-bottom: 4px; }
  .card-details .gap { height: 4px; }
  .card-details .contact-line svg { width: 4px; height: 4px; }
  .card-back .brand-name { position: absolute; left: 0; right: 0; top: 44px; justify-content: center; font-size: 20px; }
  .card-back .brand-dot { width: 22px; height: 22px; margin-right: 8px; }

  /* Envelope back */
  .envelope-back { left: 641px; top: 279px; width: 456px; height: 200px; border: 1px solid var(--edge); overflow: hidden; }
  .envelope-back .flap { position: absolute; left: 0; top: 0; width: 100%; height: 60px; }
  .envelope-back .flap-mark { position: absolute; left: 219px; top: 20px; width: 18px; height: 18px; border-radius: 50%; background: var(--brand-purple); }

  /* Envelope front */
  .envelope-front { left: 641px; top: 534px; width: 456px; height: 198px; border: 1px solid var(--edge); }
  .envelope-front .brand-name { position: absolute; left: 24px; top: 32px; font-size: 18px; }
  .envelope-front .brand-dot { width: 20px; height: 20px; margin-right: 7px; }
  .return-address { position: absolute; left: 60px; width: 78px; top: 70px; text-align: center; font-size: 7.4px; line-height: 10.5px; }
  .address-window { position: absolute; left: 24px; top: 131px; width: 93px; height: 37px; background: linear-gradient(135deg, var(--window-grey), #f1f0ee); }
</style>
</head>
<body>
  <svg width="0" height="0" style="position:absolute" aria-hidden="true">
    <symbol id="icon-phone" viewBox="0 0 10 10"><path d="M2 1l2 2-1 1.2c.6 1.2 1.6 2.2 2.8 2.8L7 6l2 2-1.3 1.3C4.5 9 1 5.5.7 2.3z" fill="#5b2d8e"/></symbol>
    <symbol id="icon-mail" viewBox="0 0 10 10"><rect x="1" y="2.5" width="8" height="5.5" rx=".6" fill="#5b2d8e"/><path d="M1.3 3l3.7 2.6L8.7 3" stroke="#fff" stroke-width=".8" fill="none"/></symbol>
    <symbol id="icon-web" viewBox="0 0 10 10"><circle cx="5" cy="5" r="4" fill="#5b2d8e"/><path d="M1 5h8M5 1c-2 2.5-2 5.5 0 8M5 1c2 2.5 2 5.5 0 8" stroke="#fff" stroke-width=".6" fill="none"/></symbol>
  </svg>

  <section class="sheet letterhead">
    <div class="brand-name"><span class="brand-dot"></span>Veloria Capital</div>
    <div class="contact-rule"></div>
    <div class="contact">
      <div>Your address, City</div>
      <div>State, Zip 1234</div>
      <div class="gap"></div>
      <div class="contact-line"><svg><use href="#icon-phone"/></svg>123 456 789</div>
      <div class="contact-line"><svg><use href="#icon-mail"/></svg>info@yourgmail.com</div>
      <div class="contact-line"><svg><use href="#icon-web"/></svg>www.yourwebsite.com</div>
    </div>
    <div class="letter-body">
      <p class="date">January-03-2020</p>
      <p class="block">Mr, Paul Avery<br>President</p>
      <p class="block">Northfield Corporation<br>123 Street Name, Suite# 10<br>City, State, 120023</p>
      <p class="salutation">Dear Mr, Paul</p>
      <p>Lorem ipsum dolor sit amet, consectetur adipiscing elit, sed do eiusmod tempor incididunt ut labore et dolore magna aliqua. Ut enim ad minim veniam, quis nostrud exercitation ullamco laboris nisi ut aliquip ex ea commodo consequat. Duis aute irure dolor in reprehenderit in voluptate velit esse cillum dolore eu fugiat nulla pariatur.</p>
      <p>Lorem ipsum dolor sit amet, consectetur adipiscing elit, sed do eiusmod tempor incididunt ut labore et dolore magna aliqua. Ut enim ad minim veniam, quis nostrud exercitation ullamco laboris nisi ut aliquip ex ea commodo consequat. Duis aute irure dolor in reprehenderit in voluptate velit esse cillum dolore eu fugiat nulla pariatur.</p>
      <p>Lorem ipsum dolor sit amet, consectetur adipiscing elit, sed do eiusmod tempor incididunt ut labore et dolore magna aliqua. Ut enim ad minim veniam, quis nostrud exercitation ullamco laboris nisi ut aliquip ex ea commodo consequat.</p>
      <p>Excepteur sint occaecat cupidatat non proident, sunt in culpa qui officia deserunt mollit anim id est laborum. re et dolore magnam aliquam quaerat voluptatem.</p>
      <p class="block regards">Regards</p>
    </div>
    <div class="signature">Laura Bennett</div>
  </section>

  <section class="sheet card card-front">
    <div class="brand-name"><span class="brand-dot"></span>Veloria Capital</div>
    <div class="card-rule"></div>
    <div class="card-details">
      <div class="person">DANIEL REYES</div>
      <div class="role">MANAGING DIRECTOR</div>
      <div class="contact-line"><svg><use href="#icon-phone"/></svg>123 456 789</div>
      <div class="contact-line"><svg><use href="#icon-mail"/></svg>info@yourgmail.com</div>
      <div class="contact-line"><svg><use href="#icon-web"/></svg>www.yourwebsite.com</div>
      <div class="gap"></div>
      <div>Your address, City</div>
      <div>State, Zip 1234</div>
    </div>
  </section>

  <section class="sheet card card-back">
    <div class="brand-name"><span class="brand-dot"></span>Veloria Capital</div>
  </section>

  <section class="sheet envelope-back">
    <svg class="flap" viewBox="0 0 456 60" preserveAspectRatio="none" aria-hidden="true">
      <path d="M0 0V20Q0 60 40 60H416Q456 60 456 20V0" fill="#fff" stroke="#d4d4d4" stroke-width="1"/>
    </svg>
    <div class="flap-mark"></div>
  </section>

  <section class="sheet envelope-front">
    <div class="brand-name"><span class="brand-dot"></span>Veloria Capital</div>
    <div class="return-address">Your address, City<br>State, Zip 1234</div>
    <div class="address-window"></div>
  </section>
</body>
</html>
```